Business Card Design

We are a commercial real estate brokerage in San Francisco, leasing office buildings downtown.
I would like a clean, elegant look. Simple but powerful .

Industry/Entity Type

Business

Contact Information for Business Card

Derek Holloway
lic# 07258143
415.555.0172
derek@velt-commercial.example
velt-commercial.example

```html
<!DOCTYPE html>
<html lang="en">
<head>
<meta charset="utf-8">
<title>Velt Commercial – Business Card</title>
<link href="https://fonts.googleapis.com/css2?family=Source+Sans+3:wght@400;600&display=swap" rel="stylesheet">
<style>
  :root {
    --stage: #e6e4e0;
    --card: #ffffff;
    --slate: #8591ad;
    --slate-light: #c9d0de;
    --charcoal: #4a4a4a;
    --ink: #6d6d6d;
    --art-dark: #5a5a5a;
    --art-light: #b9b9b9;
  }
  * { margin: 0; padding: 0; box-sizing: border-box; }
  html, body { width: 1200px; height: 950px; overflow: hidden; }
  body {
    background: var(--stage);
    font-family: "Source Sans 3", "Myriad Pro", Arial, sans-serif;
    position: relative;
  }
  .card {
    position: absolute;
    width: 560px;
    height: 320px;
    background: var(--card);
    box-shadow: 0 10px 28px rgba(0,0,0,0.18);
    overflow: hidden;
  }
  .card--back { left: 110px; top: 90px; }
  .card--front { left: 530px; top: 520px; }

  /* back side */
  .skyline-art {
    position: absolute;
    left: 180px; top: 62px;
    width: 200px; height: 120px;
    background: linear-gradient(180deg, var(--art-light), var(--art-dark));
    border-radius: 2px;
  }
  .tagline {
    position: absolute;
    left: 0; right: 0; top: 200px;
    text-align: center;
    color: var(--ink);
    font-size: 15px;
    line-height: 1.35;
  }

  /* front side */
  .top-band {
    position: absolute;
    left: 230px; right: 0; top: 38px;
    height: 38px;
    background: linear-gradient(90deg, var(--slate) 0%, var(--slate-light) 55%, var(--slate) 100%);
  }
  .top-band__cap {
    position: absolute;
    right: 0; top: 0;
    width: 78px; height: 100%;
    background: var(--charcoal);
    border-left: 3px solid var(--card);
  }
  .brand {
    position: absolute;
    left: 28px; top: 104px;
    display: flex; align-items: center;
  }
  .brand__art {
    width: 88px; height: 60px;
    background: linear-gradient(180deg, var(--art-light), var(--art-dark));
  }
  .brand__rule {
    width: 1px; height: 62px;
    background: var(--charcoal);
    margin: 0 12px;
  }
  .brand__name {
    color: var(--slate);
    font-size: 30px;
    font-weight: 600;
    letter-spacing: 1px;
    line-height: 1;
  }
  .name-band {
    position: absolute;
    left: 0; top: 188px;
    width: 400px; height: 34px;
    background: var(--slate);
    color: #fff;
    font-size: 19px;
    letter-spacing: 0.5px;
    padding: 5px 0 0 32px;
    text-transform: uppercase;
  }
  .contact {
    position: absolute;
    left: 32px; top: 236px;
    list-style: none;
    color: var(--ink);
    font-size: 15px;
    line-height: 1.3;
  }
</style>
</head>
<body>
  <section class="card card--back">
    <div class="skyline-art" role="img" aria-label="Illustration of downtown office towers"></div>
    <p class="tagline">commercial real estate brokerage in San Francisco<br>leasing office buildings downtown.</p>
  </section>

  <section class="card card--front">
    <div class="top-band"><div class="top-band__cap"></div></div>
    <div class="brand">
      <div class="brand__art" role="img" aria-label="Small illustration of office towers"></div>
      <div class="brand__rule"></div>
      <div class="brand__name">VELT COMMERCIAL</div>
    </div>
    <div class="name-band">Derek Holloway</div>
    <ul class="contact">
      <li>PH : 415.555.0172</li>
      <li>derek@velt-commercial.example</li>
      <li>www.velt-commercial.example</li>
      <li>lic# 07258143</li>
    </ul>
  </section>
</body>
</html>
```